Company identity deisgn should support 2 languages

I would like to get our company identity design
This includes the following only
Business Cards 2 languages Arabic and English
Email signature
Letterhead
Linkedin profile images
Attached is the logo in Ai format

Requirements
Must have
• For business card
Must have
Name and Adrees in arabic
Name and Address in english
You might use both side of the card
Should not have
• Any pictures other than the logo

```html
<!DOCTYPE html>
<html lang="en">
<head>
<meta charset="utf-8">
<title>Nexora Systems – Business Cards</title>
<link rel="stylesheet" href="https://fonts.googleapis.com/css2?family=Poppins:wght@400;500;600&family=Cairo:wght@400;600&display=swap">
<style>
  :root{
    --bg:#e6e7e9;
    --card:#ffffff;
    --blue:#1673bd;
    --grey-band:#bcbec2;
    --text:#3a3a3c;
    --muted:#8c8d90;
    --faint:#e8f1f8;
  }
  *{box-sizing:border-box;margin:0;padding:0}
  html,body{width:1200px;height:1200px;overflow:hidden;background:var(--bg)}
  body{position:relative;font-family:"Poppins",sans-serif;color:var(--text)}
  .card{position:absolute;left:200px;width:800px;height:457px;background:var(--card);border-radius:30px;overflow:hidden;box-shadow:0 4px 14px rgba(0,0,0,.12)}
  .card--en{top:103px}
  .card--ar{top:640px}
  .card__decor{position:absolute;right:-60px;top:40px;width:420px;height:420px;border-radius:50%;background:var(--faint);opacity:.7}
  .card__band{position:absolute;left:0;bottom:0;width:800px;height:20px}
  .brand{position:absolute;left:40px;top:62px;display:flex;align-items:center;gap:14px}
  .brand__dot{width:40px;height:40px;border-radius:50%;background:var(--blue)}
  .brand__name{font-size:28px;font-weight:600;color:var(--blue);letter-spacing:1px}
  .address{position:absolute;left:40px;top:238px;font-size:18px;line-height:23px}
  .contacts{position:absolute;left:40px;top:300px;list-style:none;font-size:18.5px;line-height:22.6px}
  .contacts li{display:flex;align-items:center;gap:10px}
  .contacts svg{width:16px;height:16px;fill:var(--blue);flex:none}
  .person{position:absolute;right:40px;top:298px;text-align:right}
  .person__name{font-size:26px;font-weight:600;color:var(--blue);letter-spacing:.3px}
  .person__role{font-size:18px;color:var(--muted);margin-top:-2px}
  .card--ar .address{font-family:"Cairo",sans-serif;direction:rtl;text-align:left;left:50px;top:228px;font-size:17px;line-height:28px}
  .card--ar .contacts{left:50px;top:290px}
  .card--ar .brand{left:50px}
  .card--ar .person{font-family:"Cairo",sans-serif;top:282px;direction:rtl}
  .card--ar .person__name{font-size:26px}
</style>
</head>
<body>

<section class="card card--en">
  <div class="card__decor"></div>
  <div class="brand"><span class="brand__dot"></span><span class="brand__name">NEXORA SYSTEMS</span></div>
  <p class="address">4120 Willow Crest Road<br>Juneau, Alaska 34811</p>
  <ul class="contacts">
    <li><svg viewBox="0 0 16 16"><path d="M3 1l3 1 1 3-2 1.5a9 9 0 0 0 4.5 4.5L11 9l3 1 1 3-2 2C7 15 1 9 1 3z"/></svg>555-214-7730</li>
    <li><svg viewBox="0 0 16 16"><path d="M4 0h8a1 1 0 0 1 1 1v14a1 1 0 0 1-1 1H4a1 1 0 0 1-1-1V1a1 1 0 0 1 1-1zm1 2v10h6V2z"/></svg>555-608-1942</li>
    <li><svg viewBox="0 0 16 16"><path d="M4 1h8v4H4zM1 6h14v7H1zm3 4h8v5H4z"/></svg>555-377-4056</li>
    <li><svg viewBox="0 0 16 16"><path d="M1 3h14v10H1zm1 1.5V5l6 4 6-4v-.5z"/></svg>hello@nexorasystems.com</li>
    <li><svg viewBox="0 0 16 16"><circle cx="8" cy="8" r="7"/></svg>www.nexorasystems.com</li>
  </ul>
  <div class="person">
    <p class="person__name">DANIEL HARPER</p>
    <p class="person__role">President</p>
  </div>
  <svg class="card__band" viewBox="0 0 800 20" preserveAspectRatio="none">
    <polygon points="0,0 510,0 505,20 0,20" fill="var(--blue)"/>
    <polygon points="514,0 800,0 800,20 509,20" fill="var(--grey-band)"/>
  </svg>
</section>

<section class="card card--ar">
  <div class="card__decor"></div>
  <div class="brand"><span class="brand__dot"></span><span class="brand__name">NEXORA SYSTEMS</span></div>
  <p class="address">4120 ويلو كريست<br>جونو، ألاسكا 34811</p>
  <ul class="contacts">
    <li><svg viewBox="0 0 16 16"><path d="M3 1l3 1 1 3-2 1.5a9 9 0 0 0 4.5 4.5L11 9l3 1 1 3-2 2C7 15 1 9 1 3z"/></svg>555-214-7730</li>
    <li><svg viewBox="0 0 16 16"><path d="M4 0h8a1 1 0 0 1 1 1v14a1 1 0 0 1-1 1H4a1 1 0 0 1-1-1V1a1 1 0 0 1 1-1zm1 2v10h6V2z"/></svg>555-608-1942</li>
    <li><svg viewBox="0 0 16 16"><path d="M4 1h8v4H4zM1 6h14v7H1zm3 4h8v5H4z"/></svg>555-377-4056</li>
    <li><svg viewBox="0 0 16 16"><path d="M1 3h14v10H1zm1 1.5V5l6 4 6-4v-.5z"/></svg>hello@nexorasystems.com</li>
    <li><svg viewBox="0 0 16 16"><circle cx="8" cy="8" r="7"/></svg>www.nexorasystems.com</li>
  </ul>
  <div class="person">
    <p class="person__name">دانيال هاربر</p>
    <p class="person__role">رئيس</p>
  </div>
  <svg class="card__band" viewBox="0 0 800 20" preserveAspectRatio="none">
    <polygon points="0,0 485,0 480,20 0,20" fill="var(--blue)"/>
    <polygon points="489,0 800,0 800,20 484,20" fill="var(--grey-band)"/>
  </svg>
</section>

</body>
</html>
```